Lawn care business card

I am looking for a quality designed personal business card to represent the quality and elegant nature of our company. We separate ourselves in our market by the aesthetic value of our work, so I am looking for marketing material that does the same. We target our marketing high end customers, and we try to avoid price shoppers. I am open to all design options, so long as they are in line with our companies values.

We are tend to go with a retro look on everything from our logo and print material, to our uniforms. We like to portray and "old fashion" set of core values, with a modern elegance. So a wild and crazy look is out of the question.

Things I'd like on the card:
1.) Logo
2.) Phone number: (816) 555-2931
3.) Website: Verdelynkc.com
4.) Email: robertfairley@verdelynkc.com
5.) My name: Robert Fairley
6.) Facebook link: facebook.com/VerdelynGardenandGrounds
7.) Instagram: http://instagram.com/verdelynkc

Attached is a copy of our logo.

Reason: More time is needed to gather conclusive feedback from the members of our marketing team.

```html
<!DOCTYPE html>
<html lang="en">
<head>
<meta charset="utf-8">
<title>Verdelyn Garden and Grounds — Business Card</title>
<link rel="stylesheet" href="https://fonts.googleapis.com/css2?family=Lato:wght@400;700;900&display=swap">
<style>
  :root {
    --backdrop: #3a3a3a;
    --card: #f4f4f4;
    --ink: #1f1f1f;
    --ink-soft: #2c2c2c;
    --accent: #e8621d;
    --rule: #2a2a2a;
  }
  * { box-sizing: border-box; margin: 0; padding: 0; }
  html, body {
    width: 1200px;
    height: 1116px;
    overflow: hidden;
    background: var(--backdrop);
    font-family: "Lato", Arial, sans-serif;
  }
  .canvas {
    position: relative;
    width: 1200px;
    height: 1116px;
    display: flex;
    align-items: center;
    justify-content: center;
  }
  .business-card {
    position: relative;
    width: 1000px;
    height: 572px;
    background: var(--card);
    border-radius: 34px;
    box-shadow: 0 18px 40px rgba(0,0,0,0.45);
  }
  .brand {
    position: absolute;
    left: 70px;
    top: 92px;
    display: flex;
    align-items: center;
    gap: 18px;
  }
  .brand-dot {
    width: 46px;
    height: 46px;
    border-radius: 50%;
    background: var(--accent);
  }
  .brand-name {
    font-weight: 900;
    font-size: 58px;
    letter-spacing: 2px;
    color: var(--ink);
    text-transform: uppercase;
  }
  .person {
    position: absolute;
    right: 70px;
    top: 214px;
    width: 440px;
    text-align: right;
  }
  .person-name {
    font-weight: 900;
    font-size: 30px;
    letter-spacing: 0.5px;
    color: var(--accent);
    text-transform: uppercase;
  }
  .person-role {
    font-weight: 700;
    font-size: 19px;
    color: var(--ink-soft);
    margin-top: 2px;
    padding-bottom: 8px;
    border-bottom: 3px solid var(--rule);
  }
  .divider {
    position: absolute;
    left: 70px;
    right: 70px;
    top: 330px;
    height: 3px;
    background: var(--rule);
  }
  .contact-list, .social-list {
    position: absolute;
    list-style: none;
    top: 356px;
  }
  .contact-list { left: 70px; }
  .social-list { right: 70px; }
  .contact-item, .social-item {
    display: flex;
    align-items: center;
    gap: 16px;
    font-weight: 700;
    font-size: 20px;
    color: var(--ink-soft);
    height: 40px;
    white-space: nowrap;
  }
  .social-item { justify-content: flex-end; }
  .contact-icon { width: 22px; height: 22px; flex: none; }
  .social-mark {
    width: 16px;
    height: 16px;
    background: var(--accent);
    border-radius: 3px;
    flex: none;
  }
</style>
</head>
<body>
<main class="canvas">
  <article class="business-card">
    <div class="brand">
      <span class="brand-dot"></span>
      <span class="brand-name">Verdelyn</span>
    </div>

    <div class="person">
      <p class="person-name">Robert Fairley</p>
      <p class="person-role">Founder / Owner</p>
    </div>

    <div class="divider"></div>

    <ul class="contact-list">
      <li class="contact-item">
        <svg class="contact-icon" viewBox="0 0 24 24" aria-hidden="true">
          <path fill="#e8621d" d="M6.6 10.8a15 15 0 0 0 6.6 6.6l2.2-2.2a1 1 0 0 1 1-.25 11.4 11.4 0 0 0 3.6.57 1 1 0 0 1 1 1V20a1 1 0 0 1-1 1A17 17 0 0 1 3 4a1 1 0 0 1 1-1h3.5a1 1 0 0 1 1 1c0 1.25.2 2.45.57 3.57a1 1 0 0 1-.25 1z"/>
        </svg>
        <span>(816) 555-2931</span>
      </li>
      <li class="contact-item">
        <svg class="contact-icon" viewBox="0 0 24 24" aria-hidden="true">
          <g fill="none" stroke="#e8621d" stroke-width="2.6" stroke-linecap="round">
            <path d="M10 14a4 4 0 0 0 5.7 0l3.5-3.5a4 4 0 0 0-5.7-5.7L12 6.3"/>
            <path d="M14 10a4 4 0 0 0-5.7 0l-3.5 3.5a4 4 0 0 0 5.7 5.7L12 17.7"/>
          </g>
        </svg>
        <span>www.verdelynkc.com</span>
      </li>
      <li class="contact-item">
        <svg class="contact-icon" viewBox="0 0 24 24" aria-hidden="true">
          <rect x="2" y="5" width="20" height="14" rx="1.5" fill="#e8621d"/>
          <path d="M3 6.5l9 6.5 9-6.5" fill="none" stroke="#f4f4f4" stroke-width="1.8"/>
        </svg>
        <span>robertfairley@verdelynkc.com</span>
      </li>
    </ul>

    <ul class="social-list">
      <li class="social-item">
        <span class="social-mark"></span>
        <span>snapgallery.net/verdelynkc</span>
      </li>
      <li class="social-item">
        <span class="social-mark"></span>
        <span>friendpage.net/VerdelynGardenandGrounds</span>
      </li>
    </ul>
  </article>
</main>
</body>
</html>
```